Camp Thornbrook 2021 Magazine Design

We are for someone to design our annual magazine/newsletter. This is a print newsletter that is a total of 20 pages. It will need to be designed in a way that is easy to share with our printers. The designer will need to be someone who is creative and easy to work with.
For those interested in this project we ask that you design 4 to 6 pages for us to view. Once we select the designer we will want the rest created in a two-week time span. For those submitting a bid please include front cover, theme & dates, mission & vision, and Make the Difference.

This link will provide the layout of the newsletter https://files.parcelvault.example/doc/7qzRk2LmVt9XwPa4NbHc6DsYe3FuJg8KoTiW5rQx/edit?share=1.

This link will provide you with the pictures that are needed and a few documents https://files.parcelvault.example/folders/4TpWx8QnRb2ZyLc7MfVd5HsJ?share=1

Details:
20 pages long (including covers)
8.5 x 11

Please message me if you need any further details.

Target Market(s)

Our alumni base. Covers all ages

Requirements
Must have
• Spelled out in document
Nice to have
• Spelled out in document
Should not have
• Spelled out in document

```html
<!DOCTYPE html>
<html lang="en">
<head>
<meta charset="utf-8">
<title>Camp Thornbrook Magazine – Where Are They Now</title>
<link href="https://fonts.googleapis.com/css2?family=Oswald:wght@500&family=Lato:wght@400&display=swap" rel="stylesheet">
<style>
  :root {
    --page-bg: #ffffff;
    --spread-orange: #d9864f;
    --heading-light: #fff7ee;
    --title-peach: #fbb57c;
    --body-ink: #2b1a10;
    --photo-pool: #6fb3a8;
    --photo-dusk: #3a2c22;
  }
  * { margin: 0; padding: 0; box-sizing: border-box; }
  html, body { width: 1200px; height: 1000px; overflow: hidden; background: var(--page-bg); }
  .spread {
    position: absolute; left: 24px; top: 127px;
    width: 1152px; height: 746px;
    background: var(--spread-orange);
    font-family: "Lato", sans-serif;
    color: var(--body-ink);
  }
  .block { position: absolute; width: 247px; }
  .body-text {
    font-size: 10px; line-height: 14.15px;
    hyphens: auto; -webkit-hyphens: auto;
    letter-spacing: -0.05px;
  }
  .question {
    font-family: "Oswald", sans-serif; font-weight: 500;
    color: var(--heading-light); font-size: 13.4px; line-height: 15.8px;
  }
  .feature-title {
    font-family: "Oswald", sans-serif; font-weight: 500;
    color: var(--title-peach); font-size: 19.5px; line-height: 23px;
    text-align: center;
  }
  .photo { position: absolute; }
  .hero { left: 34px; top: 34px; width: 508px; height: 322px;
    background: linear-gradient(100deg, #5a3a26 0%, #9a7658 45%, #c9a27c 70%, #7b5a42 100%); }
  .photo-small { width: 117px; }
  .folio { position: absolute; top: 720px; font-size: 9px; }
</style>
</head>
<body>
<main class="spread">

  <div class="photo hero" role="img" aria-label="Portrait of a smiling bearded man in glasses and a plaid shirt inside a log cabin"></div>

  <!-- page 8, column 1 -->
  <h1 class="feature-title block" style="left:34px; top:370px; width:246px;">Where Are They Now - Interview with Evan Marsh</h1>
  <h2 class="question block" style="left:34px; top:419px; width:250px;">How did you find out about Camp Thornbrook?</h2>
  <p class="body-text block" style="left:34px; top:445px;">I think I first came because two friends from my church at the time (Cedar Ridge Coc- Jordan Ashby and Kaylee Dunmore) invited me. I had never done anything similar before, but my brother and I ended up going and I liked it, hence the multiple returns.</p>
  <h2 class="question block" style="left:34px; top:531px;">What years did you attend Thornbrook? (Camper years? Staff years and jobs?)</h2>
  <p class="body-text block" style="left:34px; top:574px;">I camped from 2005 to 2009. I used to be able to recite all the camp themes, haha. I worked 2010, 2011, and 2013. I did volunteer for the last week of 2012, just as the male lifeguard so that one of the female workers wouldn’t have to. My jobs seemed to get increasingly complex as I worked. I started as just the lifeguard for boy’s swim, which involves some maintenance and cleaning and whatnot. The next year, I was Male Staff Leader. That year was fun. I remember working with</p>

  <!-- page 8, column 2 -->
  <p class="body-text block" style="left:295px; top:369px;">Lena Pruitt and Nate Corbin. Really got close to Nate that year. Summer of 2013 I was the Day Camp Director, which was probably the hardest and most rewarding summer.</p>
  <h2 class="question block" style="left:295px; top:441px;">Of all of the jobs you did at camp, which was your favorite and why?</h2>
  <p class="body-text block" style="left:295px; top:482px;">As mentioned, probably that 2013 summer as Day Camp Director. Man. I think there was an element of heaviness knowing it was my last summer. But with that job, and any day camp job there, you see a lot of the same kids ALL summer. Which can be challenging but really allows you to build relationships with those kids. One of the pictures below is of four kids that came most all summer. There were several others, but I got</p>
  <div class="photo photo-small" style="left:295px; top:624px; height:88px; background:linear-gradient(160deg,#3f5a2c,#7d9a5a);" role="img" aria-label="Four young day campers standing together in the woods"></div>
  <p class="body-text block" style="left:429px; top:609px; width:115px;">really close to those kids. With that though, as again any day camp worker can tell you, some kids come from harder lives and they really challenge you but allow you to pour in, too.</p>
  <div class="folio" style="left:34px;">8</div>

  <!-- page 9, column 1 -->
  <h2 class="question block" style="left:610px; top:36px; width:240px;">Who is someone you grew particularly close to because of Thornbrook and how did your time together at camp impact that friendship?</h2>
  <p class="body-text block" style="left:610px; top:120px;">Well, I already mentioned Nate Corbin. I remember him as a counselor when I camped, but we definitely grew closer when we worked together. The similar jobs allowed us plenty of time doing the same kind of work. I think just that mutual job, time together, allowed us plenty of camaraderie. Also, since the job inherently is service oriented and working with kids, you get closer to someone anytime you serve with them. Even now we’ll call each other up and talk about really meaningful things for a long time. I am very thankful for that.</p>
  <div class="photo photo-small" style="left:610px; top:286px; height:154px; background:linear-gradient(170deg,#6d7a4a,#a08468);" role="img" aria-label="Campers on a forest path, one holding a slice of watermelon"></div>
  <div class="photo photo-small" style="left:741px; top:286px; height:154px; background:linear-gradient(150deg,#3a9a5a,#5a2a22);" role="img" aria-label="Young staff member in sunglasses and a green camp shirt"></div>
  <h2 class="question block" style="left:610px; top:468px;">What is one of your fondest memories of your time at Thornbrook?</h2>
  <p class="body-text block" style="left:610px; top:516px;">I remember doing a lot of goofy stuff as a Group 4 guy camper in a smaller session (I only ever camped Session 1-often there was only one boy cabin in that group). Sheep Across the River in the dark. Running down the pathway to the Dinning Hall as a cabin yelling “Maggie” for some reason. Lots of tetherball. Or even as a staff worker, putting brooms in my sleeves to act goofy (and the director walking in on me-lol), lots of time on the day camp bus, lifeguarding for day camp and some of those super cute kids. I also remember feeling like one of the first times I felt God’s presence was singing “There’s a Stirring” at night after a devo. Lots of emotion, but there was definitely more. And I won’t go into great detail here, but there were some events that let</p>

  <!-- page 9, column 2 -->
  <div class="photo photo-small" style="left:871px; top:34px; height:154px; background:linear-gradient(180deg,#5f7a48 0%,#b8b0a0 60%,var(--photo-pool) 100%);" role="img" aria-label="Camper diving into a pool while others watch from the fence"></div>
  <div class="photo photo-small" style="left:1001px; top:34px; height:154px; background:linear-gradient(170deg,#5a7a3a,#3a2a20);" role="img" aria-label="Two staff members cooking pancakes on an outdoor griddle"></div>
  <p class="body-text block" style="left:871px; top:206px;">me know “hey, I have really made an impact on this kid in a positive way.” And I won’t ever forget those.</p>
  <h2 class="question block" style="left:871px; top:249px;">What have you been doing since your time at Thornbrook?</h2>
  <p class="body-text block" style="left:871px; top:290px;">Well, lots of school, haha. While working at Thornbrook, I finished a degree at Halbrook. Then went to medical school at UMSR, then finished a residency (partly in Memphis, TN but mostly in Springfield, MO), and am now in a fellowship in Wichita, KS! Lots of traveling too, evidently. So I guess now I am technically a Family Medicine Physician but I am getting some extra training in International Medicine.</p>
  <h2 class="question block" style="left:871px; top:418px;">Any final thought you would like to share?</h2>
  <p class="body-text block" style="left:871px; top:445px;">A missions professor from Halbrook was quoted in the student Newspaper as saying something along the lines of “I believe there are few places where more eternal good is done than at summer camps.” That really impacted me, and I think there is truth in that. The ability to make impacts that last a lifetime is seen yearly at Thornbrook, but maybe the impact is deeper on the counselor/staff. The mantra of “camp is for the camper” really can refocus you into a sacrificially serving way, and that mindset can really go far. So if you have the chance to camp, do it, but if you have the chance to work DO IT.</p>
  <div class="photo photo-small" style="left:871px; top:624px; height:88px; background:linear-gradient(150deg,var(--photo-dusk),#c9a030);" role="img" aria-label="Camper in a yellow bandana and sunglasses in the dining hall"></div>
  <div class="photo photo-small" style="left:1001px; top:624px; height:88px; background:linear-gradient(160deg,#4a6a3a,#8a9a7a);" role="img" aria-label="Young man outdoors among the trees"></div>
  <div class="folio" style="right:34px;">9</div>

</main>
</body>
</html>
```